​Silver Harbor Rhythm provides personal, friendly service in a fun and high energy environment. We are based in Vermont.

We would like a card that appeals to a wide range of audiences as we do a wide range of events. Please feel free to check out our website silverharborrhythm.net for inspiration.

Target Market(s)

weddings, corporate, birthday parties, colleges

Industry/Entity Type

Business

Contact Information for Business Card

Silver Harbor Rhythm
Providing Entertainment For All Occasions
555 274 9160
silverharborrhythm@mailnest.net
silverharborrhythm.net

```html
<!DOCTYPE html>
<html lang="en">
<head>
<meta charset="utf-8">
<title>Silver Harbor Rhythm – Business Card</title>
<link rel="stylesheet" href="https://fonts.googleapis.com/css2?family=Open+Sans:wght@400;600;700&display=swap">
<style>
  :root {
    --page-bg: #ece9e4;
    --card-white: #ffffff;
    --brand-green: #2f5d10;
    --text-dark: #333333;
    --text-green: #2f5d10;
    --faint-deco: #f3e3e3;
    --on-green: #ffffff;
  }
  * { margin: 0; padding: 0; box-sizing: border-box; }
  html, body { width: 1200px; height: 829px; overflow: hidden; }
  body {
    background: var(--page-bg);
    font-family: "Open Sans", Arial, sans-serif;
    position: relative;
  }
  .card {
    position: absolute;
    top: 250px;
    width: 525px;
    height: 300px;
    box-shadow: 0 6px 18px rgba(0,0,0,0.18);
    overflow: hidden;
  }
  .card-front { left: 50px; background: var(--card-white); }
  .card-back  { left: 625px; background: var(--brand-green); }

  .front-deco {
    position: absolute;
    left: 0; bottom: 0;
    width: 100%; height: 120px;
    background: linear-gradient(180deg, rgba(243,227,227,0) 0%, var(--faint-deco) 100%);
  }
  .brand-name {
    position: absolute;
    left: 0; right: 0; top: 46px;
    text-align: center;
    font-weight: 700;
    font-size: 30px;
    letter-spacing: 1px;
    color: var(--text-green);
  }
  .brand-mark {
    display: inline-block;
    width: 14px; height: 14px;
    background: var(--text-green);
    margin-right: 10px;
    vertical-align: 3px;
  }
  .holder {
    position: absolute;
    left: 0; right: 0; top: 118px;
    text-align: center;
    font-size: 17px;
    color: var(--text-green);
    font-weight: 700;
  }
  .holder .title { font-weight: 400; color: var(--text-dark); }
  .contact {
    position: absolute;
    left: 0; right: 0; top: 158px;
    text-align: center;
    font-size: 13px;
    color: var(--text-dark);
    line-height: 26px;
  }
  .contact-item { display: inline-flex; align-items: center; gap: 5px; margin: 0 6px; }
  .contact-item svg { width: 13px; height: 13px; }

  .back-brand {
    position: absolute;
    left: 0; right: 0; top: 110px;
    text-align: center;
    font-weight: 700;
    font-size: 36px;
    letter-spacing: 1px;
    color: var(--on-green);
  }
  .back-url {
    position: absolute;
    left: 0; right: 0; bottom: 44px;
    text-align: center;
    font-size: 17px;
    letter-spacing: 1px;
    color: var(--on-green);
  }
</style>
</head>
<body>
  <section class="card card-front">
    <div class="front-deco" role="img" aria-label="Faint pale-red background decoration area"></div>
    <div class="brand-name"><span class="brand-mark"></span>Silver Harbor Rhythm</div>
    <div class="holder">Your Name, <span class="title">Title</span></div>
    <div class="contact">
      <div>
        <span class="contact-item">
          <svg viewBox="0 0 16 16"><circle cx="8" cy="8" r="8" fill="var(--text-green)"/><path d="M5 4.5l1.6-.4 1 2-1 .8a5 5 0 0 0 2.5 2.5l.8-1 2 1-.4 1.6c-3.5.3-6.8-3-6.5-6.5z" fill="#fff"/></svg>
          555 274 9160
        </span>
        <span class="contact-item">
          <svg viewBox="0 0 16 16"><circle cx="8" cy="8" r="8" fill="var(--text-green)"/><circle cx="8" cy="8" r="4.5" fill="none" stroke="#fff" stroke-width="1"/><path d="M3.5 8h9M8 3.5c-2 2.5-2 6.5 0 9M8 3.5c2 2.5 2 6.5 0 9" fill="none" stroke="#fff" stroke-width="1"/></svg>
          www.silverharborrhythm.net
        </span>
      </div>
      <div>
        <span class="contact-item">
          <svg viewBox="0 0 16 16"><circle cx="8" cy="8" r="8" fill="var(--text-green)"/><rect x="4" y="5" width="8" height="6" fill="none" stroke="#fff" stroke-width="1"/><path d="M4 5l4 3.5L12 5" fill="none" stroke="#fff" stroke-width="1"/></svg>
          silverharborrhythm@mailnest.net
        </span>
      </div>
      <div>Sreet Name, City Name, Zip Code-00000</div>
    </div>
  </section>

  <section class="card card-back">
    <div class="back-brand">Silver Harbor Rhythm</div>
    <div class="back-url">www.silverharborrhythm.net</div>
  </section>
</body>
</html>
```